Varko label design

Redesign cafe range label for lightly carbonated fruit sodas.
Existing label has not worked in the market place and needs to appeal to 18-40 year olds with an active healthy lifestyle.

Product will remain in current 330ml glass bottle and flavour profile will include current range, sparkling water. It is preferred to maintain a body label only but will consider neck label as well. No over cap concepts will be considered..

Attached final shows brand progress. It has lost its way and needs reinvigorating.

Reason: I have extended the deadline to get proper feed back from others on the designs. Thank you all for your submissions so far. Ned

```html
<!DOCTYPE html>
<html lang="en">
<head>
<meta charset="utf-8">
<title>Varko label range</title>
<link rel="stylesheet" href="https://fonts.googleapis.com/css2?family=Rokkitt:wght@700;800&family=Tinos&display=swap">
<style>
  :root {
    --page: #ffffff;
    --ink: #111111;
    --berry-soft: #c6a3db;
    --berry-core: #9227d2;
    --berry-type: #8a22c4;
    --berry-art: #b4244a;
    --orange-soft: #fcbcb6;
    --orange-core: #fb2f1c;
    --orange-type: #ee2124;
    --orange-art: #f27a5a;
    --lemon-soft: #fde97e;
    --lemon-core: #fbd925;
    --lemon-type: #f6a41c;
    --lemon-art: #e6e23a;
    --badge: #0c0c0c;
    --badge-text: #ffffff;
  }
  * { margin: 0; padding: 0; box-sizing: border-box; }
  html, body {
    width: 1200px; height: 1000px; overflow: hidden;
    background: var(--page);
  }
  .canvas { position: relative; width: 1200px; height: 1000px; }
  .label {
    position: absolute; top: 243px; width: 366px; height: 575px;
    display: grid; grid-template-columns: 107px 152px 107px;
    border-top: 1px solid var(--ink); border-left: 1px solid var(--ink);
    border-right: 1px solid var(--ink);
    overflow: hidden;
  }
  .label--berry  { left: 27px; }
  .label--orange { left: 415px; }
  .label--lemon  { left: 805px; border: none; }
  .side-strip { height: 100%; }
  .core-band { position: relative; height: 100%; }
  .label--berry .side-strip  { background: var(--berry-soft); }
  .label--berry .core-band   { background: var(--berry-core); }
  .label--orange .side-strip { background: var(--orange-soft); }
  .label--orange .core-band  { background: var(--orange-core); }
  .label--lemon .side-strip  { background: var(--lemon-soft); }
  .label--lemon .core-band   { background: var(--lemon-core); }

  .flavour-name {
    position: absolute; bottom: 18px;
    writing-mode: vertical-rl; transform: rotate(180deg);
    font-family: "Rokkitt", Georgia, serif; font-weight: 800;
    line-height: 1; white-space: nowrap; letter-spacing: 0.5px;
  }
  .label--berry .flavour-name  { left: 68px; font-size: 36px; color: var(--berry-type); bottom: 20px; }
  .label--orange .flavour-name { left: 60px; font-size: 50px; color: var(--orange-type); bottom: 12px; }
  .label--lemon .flavour-name  { left: 60px; font-size: 50px; color: var(--lemon-type); bottom: 26px; }

  .brand-badge {
    position: absolute; top: 43px; left: 50%; transform: translateX(-50%);
    width: 84px; height: 84px; border-radius: 50%;
    background: var(--badge);
    display: flex; align-items: center; justify-content: center;
  }
  .brand-name {
    font-family: "Tinos", "Times New Roman", serif;
    font-size: 22px; color: var(--badge-text);
  }
  .fruit-art {
    position: absolute; left: 50%; transform: translateX(-50%);
    border-radius: 40%;
  }
  .label--berry .fruit-art  { top: 232px; width: 146px; height: 128px;
    background: radial-gradient(circle at 45% 40%, #c2283f, var(--berry-art) 55%, #e9406a); }
  .label--orange .fruit-art { top: 238px; width: 140px; height: 100px;
    background: radial-gradient(circle at 40% 55%, #ff9a86, var(--orange-art) 60%, #f39a3a); }
  .label--lemon .fruit-art  { top: 228px; width: 110px; height: 88px;
    background: radial-gradient(circle at 60% 55%, #f4f59a, var(--lemon-art) 70%, #8fcf3a); }

  .tagline {
    position: absolute; left: -20px; right: -20px; text-align: center;
    font-family: "Tinos", "Times New Roman", serif; font-size: 21px;
    color: var(--ink); white-space: nowrap;
  }
  .label--berry .tagline  { top: 374px; font-size: 19px; }
  .label--orange .tagline { top: 354px; }
  .label--lemon .tagline  { top: 342px; }
  .volume {
    position: absolute; top: 535px; width: 100%; text-align: center;
    font-family: "Tinos", "Times New Roman", serif; font-size: 14px; color: var(--ink);
  }
</style>
</head>
<body>
<main class="canvas">

  <section class="label label--berry">
    <div class="side-strip" role="img" aria-label="Pattern of sketched raspberry sprigs"></div>
    <div class="core-band">
      <div class="brand-badge"><span class="brand-name">Varko</span></div>
      <div class="fruit-art" role="img" aria-label="Cranberries and raspberries with leaves"></div>
      <p class="tagline">“the goody goody”</p>
    </div>
    <div class="side-strip" role="img" aria-label="Pattern of sketched raspberry sprigs"></div>
    <h2 class="flavour-name">RASPBERRY &amp; CRANBERRY</h2>
  </section>

  <section class="label label--orange">
    <div class="side-strip" role="img" aria-label="Pattern of sketched orange halves"></div>
    <div class="core-band">
      <div class="brand-badge"><span class="brand-name">Varko</span></div>
      <div class="fruit-art" role="img" aria-label="Blood oranges, whole and halved, with leaves"></div>
      <p class="tagline">“the rude one”</p>
      <p class="volume">330ml</p>
    </div>
    <div class="side-strip" role="img" aria-label="Pattern of sketched orange halves"></div>
    <h2 class="flavour-name">BLOOD ORANGE</h2>
  </section>

  <section class="label label--lemon">
    <div class="side-strip" role="img" aria-label="Pattern of sketched lemon branches"></div>
    <div class="core-band">
      <div class="brand-badge"><span class="brand-name">Varko</span></div>
      <div class="fruit-art" role="img" aria-label="Lemon with a cut half and leaves"></div>
      <p class="tagline">“the fancy one”</p>
      <p class="volume">330ml</p>
    </div>
    <div class="side-strip" role="img" aria-label="Pattern of sketched lemon branches"></div>
    <h2 class="flavour-name">LEMONCELLO</h2>
  </section>

</main>
</body>
</html>
```